Ram and co fleecing works pty ltd

We are sheep shearing contractors,we are looking for a simple design business card, with a drawing like picture of a Australian sheep on it, then just standard details, name, phone, email, po box.
We would like double sided, with 2 lines of wiriting on the back, no bright colours please.
We like black and white, doesn't have to be too serious, however nothing to far left of cwntre.
On the back of the card we would like professional shearing contract offering full contract team.
Can use use the symbol & in the name instead of and.

Target Market(s)

Sheep farmers, target males from age 20 and up

Contact Information for Business Card

Company name ram and co fleecing works pty ltd
Marcus haldenby 0471305846, po box 4072 sale vic 3853,
Email ramandcofleecing@mailbarn.example, gippsland shearing contractor

Font styles to use
Serif

Colors

Designer to choose only greyscale colors for use in the design.

Requirements
Nice to have
• Simple design

```html
<!DOCTYPE html>
<html lang="en">
<head>
<meta charset="utf-8">
<title>Ram and Co Fleecing Works – Business Card</title>
<link href="https://fonts.googleapis.com/css2?family=Archivo:wght@800&family=Arimo:wght@400;700&display=swap" rel="stylesheet">
<style>
  :root {
    --bg: #2b2b2b;
    --paper: #ffffff;
    --ink: #1a1a1a;
    --card-dark: #0d0d0d;
    --rule: #9a9a9a;
    --muted: #3a3a3a;
    --light: #f2f2f2;
  }
  html, body {
    margin: 0;
    padding: 0;
    width: 1200px;
    height: 900px;
    overflow: hidden;
    background: var(--bg);
  }
  .canvas {
    position: relative;
    width: 1200px;
    height: 900px;
  }
  .card {
    position: absolute;
    left: 250px;
    width: 700px;
    height: 400px;
    box-sizing: border-box;
    box-shadow: 0 10px 30px rgba(0,0,0,.5);
    overflow: hidden;
  }
  .card--front { top: 30px; background: var(--paper); color: var(--ink); }
  .card--back { top: 470px; background: var(--card-dark); color: var(--light); }

  .wordmark {
    font-family: "Archivo", "Arial Black", sans-serif;
    font-weight: 800;
    text-transform: uppercase;
    line-height: 1;
    margin: 0;
  }
  .wordmark__main { display: block; font-size: 50px; letter-spacing: 1px; }
  .wordmark__sub { display: block; font-size: 17px; letter-spacing: .5px; margin-top: 6px; }

  .card--front .wordmark { position: absolute; left: 150px; top: 70px; color: var(--ink); }
  .tagline {
    position: absolute;
    left: 150px;
    top: 170px;
    margin: 0;
    font-family: "Arimo", Arial, sans-serif;
    font-weight: 700;
    font-size: 19px;
    text-transform: uppercase;
    letter-spacing: .3px;
  }
  .write-line {
    position: absolute;
    left: 150px;
    width: 420px;
    height: 0;
    border-top: 1px solid var(--rule);
  }
  .write-line--one { top: 235px; }
  .write-line--two { top: 290px; }
  .service-note {
    position: absolute;
    right: 40px;
    bottom: 34px;
    margin: 0;
    font-family: "Arimo", Arial, sans-serif;
    font-size: 18px;
    color: var(--muted);
  }

  .card--back .wordmark { position: absolute; left: 44px; top: 92px; color: var(--light); }
  .card--back .wordmark__main { font-size: 42px; }
  .card--back .wordmark__sub { font-size: 14px; }
  .contact-name {
    position: absolute;
    left: 44px;
    top: 222px;
    margin: 0;
    font-family: "Archivo", Arial, sans-serif;
    font-weight: 800;
    font-size: 22px;
    text-transform: uppercase;
    letter-spacing: .5px;
  }
  .contact-list {
    position: absolute;
    left: 44px;
    top: 262px;
    margin: 0;
    padding: 0;
    list-style: none;
    font-family: "Arimo", Arial, sans-serif;
    font-size: 17px;
    z-index: 1;
  }
  .contact-list li { display: flex; align-items: center; height: 28px; white-space: nowrap; }
  .contact-list svg { width: 18px; height: 18px; margin-right: 12px; flex: none; }
  .contact-list .contact-post { margin-top: 16px; }
  .sheep-art {
    position: absolute;
    right: 24px;
    top: 36px;
    width: 250px;
    height: 330px;
    background: radial-gradient(ellipse at 50% 45%, #3c3c3c 0%, #1c1c1c 70%, var(--card-dark) 100%);
    border-radius: 8px;
  }
</style>
</head>
<body>
<main class="canvas">
  <section class="card card--front" aria-label="Card front">
    <h1 class="wordmark">
      <span class="wordmark__main">Ram and Co</span>
      <span class="wordmark__sub">Fleecing Works Pty Ltd</span>
    </h1>
    <p class="tagline">Gippsland Shearing Contractor</p>
    <div class="write-line write-line--one"></div>
    <div class="write-line write-line--two"></div>
    <p class="service-note">Professional shearing contract offering full contract team.</p>
  </section>

  <section class="card card--back" aria-label="Card back">
    <h2 class="wordmark">
      <span class="wordmark__main">Ram and Co</span>
      <span class="wordmark__sub">Fleecing Works Pty Ltd</span>
    </h2>
    <p class="contact-name">Marcus Haldenby</p>
    <ul class="contact-list">
      <li>
        <svg viewBox="0 0 24 24" aria-hidden="true"><path d="M6.6 10.8c1.4 2.8 3.8 5.1 6.6 6.6l2.2-2.2c.3-.3.7-.4 1-.2 1.1.4 2.3.6 3.6.6.6 0 1 .4 1 1V20c0 .6-.4 1-1 1C10.6 21 3 13.4 3 4c0-.6.4-1 1-1h3.5c.6 0 1 .4 1 1 0 1.3.2 2.5.6 3.6.1.3 0 .7-.2 1l-2.3 2.2z" fill="#f2f2f2"/></svg>
        0471305846
      </li>
      <li>
        <svg viewBox="0 0 24 24" aria-hidden="true"><rect x="2" y="5" width="20" height="14" fill="#f2f2f2"/><path d="M2 5l10 8 10-8" fill="none" stroke="#0d0d0d" stroke-width="1.6"/></svg>
        ramandcofleecing@mailbarn.example
      </li>
      <li class="contact-post">PO box 4072 sale vic 3853</li>
    </ul>
    <div class="sheep-art" role="img" aria-label="White line drawing of an Australian sheep standing in profile"></div>
  </section>
</main>
</body>
</html>
```